School Hallway Magnetic Display Design for school values

I am looking for a someone to help me design a magnetic hallway display that will hang in the hallway of our small school. There are several elements, including 1. 6ft by 4ft designed magnetic bulletin board, 2. Magnets that will stick to the board. See attachment for which elements belong where. The display will be for our MOBLAT program, which rewards students for demonstrating our school values. We want the display to be beautiful and interactive. We are also rebranding, so we want the design to align with our new fonts and colors. In the attached PDF is an outline of our new brand guidelines. Unfortunately, we don't have the color codes, but I'm hoping that you can match the colors listed. Attached are elements to be used on the board, but please use your creativity to make it more dynamic and visually appealing. For example, the star magnets could be another shape. The MOBLAT magnets must remain the same. I've included two photos of boards at other schools that inspired this project.

Target Market(s)

School Community

Industry/Entity Type

Education

Requirements
Should not have
• School Logo

```html
<!DOCTYPE html>
<html lang="en">
<head>
<meta charset="utf-8">
<title>MOBLAT at RVS – Hallway Values Display</title>
<link rel="stylesheet" href="https://fonts.googleapis.com/css2?family=Playfair+Display:wght@800;900&display=swap">
<style>
  :root {
    --backdrop: #444444;
    --white: #ffffff;
    --navy: #1f4e74;
    --gold: #ffdb80;
    --coral: #dd8a75;
    --coral-soft: #eaa28f;
    --lilac: #bd9cc3;
    --lilac-soft: #d7b1de;
    --sage: #d7dfb7;
    --sage-soft: #edf3d0;
    --sage-ink: #55633a;
    --sun: #ffdb80;
    --sun-soft: #f8e4b0;
    --sun-ink: #8a5a12;
    --sky: #afcde4;
    --sky-soft: #c9e4fa;
    --sky-ink: #1f4e74;
    --ocean: #2b5a91;
    --ocean-soft: #6a8db3;
    --shadow: 12px 18px 30px rgba(0, 0, 0, 0.38);
  }
  * { box-sizing: border-box; margin: 0; padding: 0; }
  html, body {
    width: 1200px;
    height: 2355px;
    overflow: hidden;
    background: var(--backdrop);
  }
  .display {
    position: relative;
    width: 1200px;
    height: 2355px;
    font-family: "Playfair Display", Georgia, serif;
  }

  /* Magnetic board */
  .board {
    position: absolute;
    left: 101px;
    top: 133px;
    width: 998px;
    height: 664px;
    background: var(--white);
    box-shadow: var(--shadow);
    overflow: hidden;
  }
  .board-motif {
    position: absolute;
    left: 0;
    top: 0;
    width: 150px;
    height: 100%;
    background: linear-gradient(180deg,
      var(--gold) 0%, var(--coral) 18%, var(--navy) 38%,
      var(--navy) 55%, var(--gold) 70%, var(--navy) 88%, var(--navy) 100%);
    opacity: 0.9;
  }
  .board-title {
    position: absolute;
    left: 186px;
    top: 52px;
    font-size: 100px;
    font-weight: 900;
    line-height: 1.2;
    letter-spacing: -1px;
    white-space: nowrap;
  }
  .board-title .program { color: var(--coral); }
  .board-title .joiner { color: var(--lilac); }
  .board-title .school { color: var(--sky); }

  /* Value magnets */
  .value-magnet {
    position: absolute;
    left: 72px;
    width: 593px;
    height: 198px;
    border-radius: 99px;
    overflow: hidden;
    box-shadow: var(--shadow);
    display: flex;
    align-items: center;
    padding-left: 35px;
  }
  .value-name {
    position: relative;
    z-index: 1;
    color: var(--white);
    font-size: 54px;
    font-weight: 900;
    letter-spacing: 0.5px;
  }
  .value-leaf {
    position: absolute;
    right: 0;
    top: 0;
    width: 208px;
    height: 100%;
  }
  .simplicity { top: 913px; background: var(--coral); }
  .simplicity .value-leaf { background: linear-gradient(135deg, transparent 25%, var(--coral-soft) 60%); }
  .peace { top: 1136px; background: var(--lilac); }
  .peace .value-leaf { background: linear-gradient(135deg, transparent 25%, var(--lilac-soft) 60%); }
  .integrity { top: 1357px; background: var(--sage); }
  .integrity .value-name { color: var(--sage-ink); }
  .integrity .value-leaf { background: linear-gradient(135deg, transparent 25%, var(--sage-soft) 60%); }
  .community { top: 1579px; background: var(--sun); }
  .community .value-name { color: var(--sun-ink); }
  .community .value-leaf { background: linear-gradient(135deg, transparent 25%, var(--sun-soft) 60%); }
  .equality { top: 1801px; background: var(--sky); }
  .equality .value-name { color: var(--sky-ink); }
  .equality .value-leaf { background: linear-gradient(135deg, transparent 25%, var(--sky-soft) 60%); }
  .stewardship { top: 2023px; background: var(--ocean); }
  .stewardship .value-leaf { background: linear-gradient(135deg, transparent 25%, var(--ocean-soft) 60%); }

  /* Progress thermometer */
  .thermometer {
    position: absolute;
    left: 0;
    top: 0;
    width: 1200px;
    height: 2355px;
    filter: drop-shadow(12px 18px 16px rgba(0, 0, 0, 0.38));
  }
  .thermometer .outline { fill: var(--white); stroke: var(--navy); stroke-width: 7; }
  .thermometer .channel { fill: none; stroke: var(--navy); stroke-width: 4; }
  .thermometer .bulb { fill: none; stroke: var(--navy); stroke-width: 3; }
  .thermometer .tick { stroke: var(--navy); stroke-width: 3; }
</style>
</head>
<body>
<main class="display">
  <section class="board">
    <div class="board-motif" role="img" aria-label="Decorative leaf and sun pattern in navy, gold and coral"></div>
    <h1 class="board-title"><span class="program">MOBLAT</span> <span class="joiner">at</span> <span class="school">RVS</span></h1>
  </section>

  <div class="value-magnet simplicity"><span class="value-name">Simplicity</span><span class="value-leaf" role="img" aria-label="Soft leaf motif"></span></div>
  <div class="value-magnet peace"><span class="value-name">Peace</span><span class="value-leaf" role="img" aria-label="Soft leaf motif"></span></div>
  <div class="value-magnet integrity"><span class="value-name">Integrity</span><span class="value-leaf" role="img" aria-label="Soft leaf motif"></span></div>
  <div class="value-magnet community"><span class="value-name">Community</span><span class="value-leaf" role="img" aria-label="Soft leaf motif"></span></div>
  <div class="value-magnet equality"><span class="value-name">Equality</span><span class="value-leaf" role="img" aria-label="Soft leaf motif"></span></div>
  <div class="value-magnet stewardship"><span class="value-name">Stewardship</span><span class="value-leaf" role="img" aria-label="Soft leaf motif"></span></div>

  <svg class="thermometer" viewBox="0 0 1313 2576" aria-label="Progress thermometer">
    <path class="outline" d="M947,1999 L947,1140 A90,90 0 0 1 1127,1140 L1127,1999 A193,193 0 1 1 947,1999 Z"/>
    <path class="channel" d="M1010,2040 L1010,1140 A26,26 0 0 1 1062,1140 L1062,2040"/>
    <circle class="bulb" cx="1037" cy="2168" r="130"/>
    <g>
      <line class="tick" x1="965" y1="1283" x2="1008" y2="1283"/>
      <line class="tick" x1="967" y1="1320" x2="992" y2="1320"/>
      <line class="tick" x1="967" y1="1358" x2="992" y2="1358"/>
      <line class="tick" x1="967" y1="1395" x2="992" y2="1395"/>
      <line class="tick" x1="965" y1="1432" x2="1008" y2="1432"/>
      <line class="tick" x1="967" y1="1470" x2="992" y2="1470"/>
      <line class="tick" x1="967" y1="1507" x2="992" y2="1507"/>
      <line class="tick" x1="967" y1="1544" x2="992" y2="1544"/>
      <line class="tick" x1="965" y1="1581" x2="1008" y2="1581"/>
      <line class="tick" x1="967" y1="1619" x2="992" y2="1619"/>
      <line class="tick" x1="967" y1="1656" x2="992" y2="1656"/>
      <line class="tick" x1="967" y1="1693" x2="992" y2="1693"/>
      <line class="tick" x1="965" y1="1730" x2="1008" y2="1730"/>
      <line class="tick" x1="967" y1="1768" x2="992" y2="1768"/>
      <line class="tick" x1="967" y1="1805" x2="992" y2="1805"/>
      <line class="tick" x1="967" y1="1842" x2="992" y2="1842"/>
      <line class="tick" x1="965" y1="1879" x2="1008" y2="1879"/>
      <line class="tick" x1="967" y1="1917" x2="992" y2="1917"/>
      <line class="tick" x1="967" y1="1954" x2="992" y2="1954"/>
      <line class="tick" x1="967" y1="1991" x2="992" y2="1991"/>
    </g>
  </svg>
</main>
</body>
</html>
```